Stationery Design Project for Nimbora, Chicago

Nimbora, a street parking application which helps car drivers find a street parking spot by offering an ideal path along which to look for parking. This path is calculated by our algorithm based on data (e.g. historical data, baseball games schedule, etc.). Along this path the driver will find a spot and will also save 70% of the search time. Customer we target is reg. between 21 and 45 yo.

We envision something young, fresh, bright and original. Slightly abstract maybe. It should represent the idea and elements of finding street parking in the city, e.g. car(s), parking spot, people, city, etc. (just ideas!).

Logo is attached.

Requirement:
- Business Cards (2 Sided Full Color CMYK)
- Letterhead (1 Sided Full Color CMYK)
- Envelope (1 Sided Full Color CMYK)
- Sticker (1 Sided Full Color CMYK), round with a 2inch diameter.

Reason: We're starting to get more and more designs and need more time to look into all of them. Very exciting!! Thanks to everybody!

Hi all, we're in the process of selecting our favs. Though choices!!! Really good submissions. Will keep you posted and sorry for the delay.

Target Market(s)

Car drivers and owners between 21 and 45

Industry/Entity Type

Parking

Requirements
Must have
• Sticker should be round and include company URL nimbora.com and the new logo which we will attach soon.
Should not have
• Should not be too serious or boring.

```html
<!DOCTYPE html>
<html lang="en">
<head>
<meta charset="utf-8">
<title>Nimbora – Business Card</title>
<link rel="stylesheet" href="https://fonts.googleapis.com/css2?family=Open+Sans:wght@400;600;700&display=swap">
<style>
  :root {
    --backdrop: #d6d6d6;
    --card: #ffffff;
    --ink: #111111;
    --wordmark: #1c1c1c;
    --brand-blue: #1f4aa8;
    --brand-blue-light: #2a78d0;
    --brand-blue-deep: #1d3796;
    --swoosh-dark: #111111;
    --swoosh-grey: #5a5a5a;
    --on-band: #ffffff;
  }
  * { box-sizing: border-box; margin: 0; padding: 0; }
  html, body {
    width: 954px; height: 1200px; overflow: hidden;
    background: var(--backdrop);
    font-family: "Open Sans", Arial, sans-serif;
    color: var(--ink);
  }
  .sheet { position: relative; width: 954px; height: 1200px; }
  .card {
    position: absolute; left: 62px; width: 796px; height: 455px;
    background: var(--card); border-radius: 28px; overflow: hidden;
    box-shadow: 0 3px 10px rgba(0,0,0,0.25);
  }
  .card--front { top: 100px; }
  .card--back { top: 648px; }
  .card__bands { position: absolute; inset: 0; width: 796px; height: 455px; }

  .brand { position: absolute; display: flex; align-items: center; }
  .brand__dot {
    border-radius: 50%;
    background: var(--brand-blue);
    flex: none;
  }
  .brand__name {
    font-weight: 600; color: var(--wordmark); letter-spacing: 1px; line-height: 1;
  }
  .card--front .brand { left: 118px; top: 52px; gap: 44px; }
  .card--front .brand__dot { width: 136px; height: 136px; }
  .card--front .brand__name { font-size: 84px; }
  .card--back .brand { left: 62px; top: 101px; gap: 46px; }
  .card--back .brand__dot { width: 168px; height: 168px; }
  .card--back .brand__name { font-size: 104px; }

  .holder {
    position: absolute; left: 0; right: 0; top: 210px;
    text-align: center; font-size: 24px; font-weight: 700;
  }
  .contact {
    position: absolute; left: 0; right: 0; top: 277px;
    text-align: center; font-size: 18px; line-height: 27px;
  }
  .contact b { font-weight: 700; }
  .contact .sep { margin: 0 6px; }
  .address {
    position: absolute; left: 268px; top: 402px;
    font-size: 19px; color: var(--on-band);
  }
  .web {
    position: absolute; left: 370px; top: 394px;
    font-size: 24px; color: var(--on-band);
  }
  .web__domain { letter-spacing: 8px; }
</style>
</head>
<body>
<main class="sheet">

  <section class="card card--front" aria-label="Business card front">
    <svg class="card__bands" viewBox="0 0 796 455" aria-hidden="true">
      <defs>
        <linearGradient id="frontBand" x1="0" x2="1" y1="0" y2="0">
          <stop offset="0" stop-color="var(--brand-blue-light)"/>
          <stop offset="1" stop-color="var(--brand-blue-deep)"/>
        </linearGradient>
        <linearGradient id="frontSwoosh" x1="0" x2="1" y1="0" y2="0">
          <stop offset="0" stop-color="var(--swoosh-grey)"/>
          <stop offset="0.6" stop-color="var(--swoosh-dark)"/>
        </linearGradient>
      </defs>
      <path d="M0 398 C120 382 280 364 410 355 C290 368 140 395 0 436 Z" fill="url(#frontSwoosh)"/>
      <path d="M14 455 C150 405 300 372 410 357 C560 352 700 368 796 395 L796 455 Z" fill="url(#frontBand)"/>
    </svg>
    <div class="brand">
      <span class="brand__dot"></span>
      <span class="brand__name">Nimbora</span>
    </div>
    <p class="holder">Your Name - Designation</p>
    <p class="contact">
      <b>t</b> : 123-456-7890<span class="sep">|</span><b>m</b> : 123-456-7890<br>
      <b>e</b> : name@website.com<span class="sep">|</span><b>w</b> : www.website.com
    </p>
    <p class="address">City Name, Street Name, State Name, Country Code</p>
  </section>

  <section class="card card--back" aria-label="Business card back">
    <svg class="card__bands" viewBox="0 0 796 455" aria-hidden="true">
      <defs>
        <linearGradient id="backBand" x1="0" x2="1" y1="0" y2="0">
          <stop offset="0" stop-color="var(--swoosh-dark)"/>
          <stop offset="0.75" stop-color="var(--swoosh-dark)"/>
          <stop offset="1" stop-color="var(--swoosh-grey)"/>
        </linearGradient>
        <linearGradient id="backSwoosh" x1="0" x2="1" y1="0" y2="0">
          <stop offset="0" stop-color="var(--brand-blue-light)"/>
          <stop offset="1" stop-color="var(--brand-blue-deep)"/>
        </linearGradient>
      </defs>
      <path d="M0 398 C120 382 280 364 410 355 C290 368 140 395 0 436 Z" fill="url(#backSwoosh)"/>
      <path d="M14 455 C150 405 300 372 410 357 C560 352 700 368 796 395 L796 455 Z" fill="url(#backBand)"/>
    </svg>
    <div class="brand">
      <span class="brand__dot"></span>
      <span class="brand__name">Nimbora</span>
    </div>
    <p class="web">www.<span class="web__domain"> WEBSITE </span>.com</p>
  </section>

</main>
</body>
</html>
```